Stationary Set Rebrand for Brennick

We are a Canadian Distribution and Service Company that was established in 1969. Over the past 5 decades we have expanded our business and have warehouses across Canada. We specialize in adhesive tapes, adhesives, films, safety, warehouse, shipping, janitorial and packaging supplies.

We have updated our logo design and would like a new corporate branding identity that includes a new fresh Stationary Set (Business Cards, Letterhead, Letterhead MS Word, Envelope, Presentation Folders, Email Signatures, Notepad Covers, etc.)

Target Market(s)

Industrial Business Sector

Font styles to use
Sans Serif

Colors
0054AA
0677BA
7BADD7
CADEEF
E8F1F8
0094D4
00A9DD
6FCCEA
C7EBF8
E9F6FB
00AB8E
00BBA5
67D7C9
C6EFE9
E9F9F6
EB3D1F
EC4F4E
F09395
F8D3D4
FCEDEE

Requirements
Should not have
• Colors not too light, darker colours preferred

```html
<!DOCTYPE html>
<html lang="en">
<head>
<meta charset="utf-8">
<title>Brennick Business Card</title>
<link href="https://fonts.googleapis.com/css2?family=Michroma&family=Saira:wght@400;500;700;800&display=swap" rel="stylesheet">
<style>
  :root {
    --brand-red: #d71920;
    --ink: #1a1a1a;
    --text-grey: #4a4a4a;
    --rule-grey: #8a8a8a;
    --card-white: #ffffff;
    --backdrop: #e4e4e4;
  }
  * { margin: 0; padding: 0; box-sizing: border-box; }
  html, body {
    width: 1200px;
    height: 1200px;
    overflow: hidden;
    background: var(--backdrop);
    font-family: "Saira", sans-serif;
  }
  .canvas { position: relative; width: 1200px; height: 1200px; }

  .card { position: absolute; width: 696px; height: 398px; }
  .card--front { left: 262px; top: 156px; background: var(--card-white); }
  .card--back { left: 258px; top: 651px; background: var(--brand-red); }

  .emblem-area {
    position: absolute;
    left: 83px; top: 57px;
    width: 270px; height: 278px;
    background: radial-gradient(circle at 50% 45%, #e02a30 0%, var(--brand-red) 70%);
    border-radius: 6px;
  }

  .divider {
    position: absolute;
    left: 378px; top: 52px;
    width: 1px; height: 286px;
    background: var(--rule-grey);
  }

  .details { position: absolute; left: 403px; top: 50px; width: 280px; }

  .wordmark {
    font-family: "Saira", sans-serif;
    font-weight: 800;
    font-size: 44px;
    line-height: 1;
    color: var(--ink);
    letter-spacing: 0.5px;
  }
  .tagline {
    font-weight: 500;
    font-size: 11.5px;
    color: var(--ink);
    margin-top: 2px;
  }

  .person-name {
    position: absolute; top: 87px;
    font-family: "Michroma", sans-serif;
    font-size: 20px;
    color: var(--brand-red);
    letter-spacing: 0.5px;
    white-space: nowrap;
  }
  .person-title {
    position: absolute; top: 114px;
    font-size: 16px;
    color: var(--text-grey);
    letter-spacing: 0.6px;
  }
  .address {
    position: absolute; top: 153px;
    font-size: 17px;
    line-height: 21px;
    color: var(--text-grey);
    letter-spacing: 0.6px;
    font-style: normal;
  }
  .contact-list {
    position: absolute; top: 206px;
    list-style: none;
  }
  .contact-list li {
    display: flex; align-items: center;
    height: 21px;
    font-size: 17px;
    color: var(--text-grey);
    letter-spacing: 0.6px;
  }
  .contact-list svg { width: 14px; height: 14px; margin-right: 13px; flex: none; }

  .back-logo {
    position: absolute;
    left: 0; right: 0; top: 128px;
    text-align: center;
    color: var(--card-white);
  }
  .back-logo .wordmark { color: var(--card-white); font-size: 104px; letter-spacing: 1px; }
  .back-logo .tagline { color: var(--card-white); font-size: 24px; font-weight: 700; margin-top: 4px; }
</style>
</head>
<body>
<main class="canvas">

  <section class="card card--front">
    <div class="emblem-area" role="img" aria-label="Large red brand leaf emblem"></div>
    <div class="divider"></div>

    <div class="details">
      <div class="wordmark">Brennick</div>
      <div class="tagline">Tape and Packaging Specialists</div>

      <div class="person-name">DANIEL HARTLEY</div>
      <div class="person-title">President</div>

      <address class="address">4120 Larchmont Road<br>Kingsford, Canada 58210</address>

      <ul class="contact-list">
        <li>
          <svg viewBox="0 0 16 16" aria-hidden="true"><path fill="#d71920" d="M3.2 1.2l2.4-.6 1.5 3.4-1.5 1.1c.8 1.9 2.1 3.3 4 4.3l1.2-1.5 3.4 1.6-.6 2.4c-.2.7-.9 1.2-1.6 1.1C6.7 12.5 3.4 9.2 2.1 3c-.1-.8.4-1.6 1.1-1.8z"/></svg>
          555-204-7381
        </li>
        <li>
          <svg viewBox="0 0 16 16" aria-hidden="true"><rect x="4" y="0.8" width="8" height="14.4" rx="1.3" fill="none" stroke="#d71920" stroke-width="1.5"/><circle cx="8" cy="12.6" r="0.9" fill="#d71920"/></svg>
          555-319-6642
        </li>
        <li>
          <svg viewBox="0 0 16 16" aria-hidden="true"><rect x="0.8" y="3" width="14.4" height="10" fill="#d71920"/><path d="M1.5 4l6.5 5 6.5-5M1.5 12.3l4.6-4.4M14.5 12.3l-4.6-4.4" fill="none" stroke="#fff" stroke-width="1.1"/></svg>
          info@brennick.com
        </li>
        <li>
          <svg viewBox="0 0 16 16" aria-hidden="true"><circle cx="8" cy="8" r="7" fill="#d71920"/><ellipse cx="8" cy="8" rx="3" ry="7" fill="none" stroke="#fff" stroke-width="1"/><path d="M1 8h14" stroke="#fff" stroke-width="1"/></svg>
          www.brennick.com
        </li>
      </ul>
    </div>
  </section>

  <section class="card card--back">
    <div class="back-logo">
      <div class="wordmark">Brennick</div>
      <div class="tagline">Tape and Packaging Specialists</div>
    </div>
  </section>

</main>
</body>
</html>
```